A website for a Maltese Law Firm

Our law firm needs a website to further its business. The site should have a simple yet effective design. We would need the following sections: About us, Practice Areas, About Malta, Contact. These should be further split as follows:

About us: Our firm, Our values, What others say, Offices

Practice Areas: Crimimal, Citizenship & Residence, Sovereign Patron Pathway, Criminal Defence, Civil Litigation, Arbitration and ADR, Commercial and Corporate, Media Law.

About Malta: just one section.

Contact: Just one section

We would also need a news feed at the front of the site to include latest news regarding our cases.

At the bottom we need a section for our Terms and a Privacy Statement.

Our logo is being attached.

Target Market(s)

All clients looking for legal assistance in Malta

Industry/Entity Type

Legal

Coding

Coded - Design and coding required

Number of Pages Required

1 page

Requirements
Must have
• It must be simple yet striking.

```html
<!DOCTYPE html>
<html lang="en">
<head>
<meta charset="utf-8">
<title>Ferris &amp; Delmar Advocates</title>
<link href="https://fonts.googleapis.com/css2?family=Lato:ital,wght@0,300;0,400;0,700;1,400&display=swap" rel="stylesheet">
<style>
:root{
  --ink:#333333;
  --muted:#8a8a8a;
  --soft:#b5b5b5;
  --line:#d6d6d6;
  --panel:#efefef;
  --white:#ffffff;
  --dark:#1c1c1c;
  --footer:#3a3a3a;
  --icon-ring:#f3f3f3;
}
*{margin:0;padding:0;box-sizing:border-box}
html,body{width:1200px;height:4627px;overflow:hidden}
body{position:relative;background:var(--white);font-family:'Lato',sans-serif;color:var(--ink)}
.abs{position:absolute}
.photo{position:absolute}

/* header */
.hero{left:0;top:0;width:1200px;height:651px;background:linear-gradient(160deg,#3d4a55 0%,#1d2630 45%,#2c2a27 75%,#4a4035 100%)}
.hero-shade{left:0;top:0;width:1200px;height:651px;background:rgba(0,0,0,.35)}
.topnav{left:0;top:0;width:1200px;height:34px;background:rgba(255,255,255,.08);border-bottom:3px solid #111;display:flex;justify-content:center;gap:34px;align-items:center}
.topnav a{color:#ddd;font-size:10px;letter-spacing:1.5px;text-transform:uppercase;text-decoration:none}
.brand{left:0;top:218px;width:1200px;text-align:center;color:var(--white)}
.brand-name{font-size:40px;font-weight:400;letter-spacing:4px;text-transform:uppercase}
.brand-sub{font-size:15px;letter-spacing:9px;text-transform:uppercase;margin-top:4px;border-top:1px solid #fff;display:inline-block;padding-top:4px}
.hero-text{left:400px;top:352px;width:400px;text-align:center;color:#e6e6e6;font-size:12px;line-height:18px}
.btn-ghost{left:546px;top:448px;width:108px;height:32px;border:2px solid var(--white);color:var(--white);font-size:11px;letter-spacing:1.5px;text-transform:uppercase;display:flex;align-items:center;justify-content:center}
.chevron{left:588px;top:520px}

/* section titles */
.section-title{left:0;width:1200px;text-align:center;font-size:22px;font-weight:400;letter-spacing:4px;text-transform:uppercase;color:var(--ink)}
.title-rule{left:580px;width:40px;height:1px;background:var(--soft)}
.intro{left:440px;top:805px;width:320px;text-align:center;font-size:11px;line-height:17px;color:var(--muted)}

/* feature rows */
.feature-panel{background:var(--panel)}
.feature-num{font-size:60px;font-weight:300;color:#c7c7c7;line-height:1}
.feature-head{font-size:17px;font-weight:400;letter-spacing:2.5px;text-transform:uppercase;color:var(--ink)}
.feature-text{font-size:12px;line-height:19px;color:var(--muted);width:380px}
.btn-small{height:22px;padding:0 12px;border:1px solid #bdbdbd;font-size:8px;letter-spacing:1px;text-transform:uppercase;color:#777;display:inline-flex;align-items:center}

/* practice areas */
.practice{width:220px;text-align:center}
.practice-icon{width:52px;height:52px;border-radius:50%;background:var(--icon-ring);margin:0 auto;display:flex;align-items:center;justify-content:center}
.practice-name{margin-top:18px;font-size:16px;letter-spacing:3px;text-transform:uppercase;color:#555}
.practice-text{margin:10px auto 0;width:180px;font-size:9px;line-height:14px;color:var(--soft)}

/* bands */
.band{left:0;width:1200px;border-top:4px solid #111;border-bottom:4px solid #111}
.band-title{left:0;width:1200px;text-align:center;color:var(--white);font-size:20px;font-weight:700}
.band-text{left:380px;width:440px;text-align:center;color:#f2f2f2;font-size:12px;line-height:17px;font-style:italic;font-weight:700}
.band-author{left:0;width:1200px;text-align:center;color:#ddd;font-size:11px;font-style:italic}
.arrow{color:var(--white);font-size:22px}

/* news */
.news-title{font-size:20px;font-weight:400;color:var(--ink)}
.news-text{width:380px;font-size:12px;line-height:18px;color:var(--muted)}

/* contact */
.field-label{font-size:9px;letter-spacing:1px;text-transform:uppercase;color:#666}
.field{background:var(--panel)}
.contact-side{font-size:10px;line-height:16px;color:var(--muted)}
.social-dot{width:10px;height:10px;border-radius:50%;background:#9a9a9a;display:inline-block;margin-right:8px}

/* footer */
.site-footer{left:0;top:4458px;width:1200px;height:169px;background:var(--footer)}
.footer-brand{left:0;top:4496px;width:1200px;text-align:center;color:var(--white);font-size:20px;letter-spacing:3px;text-transform:uppercase}
.footer-nav{left:0;top:4558px;width:1200px;display:flex;justify-content:center;gap:22px}
.footer-nav a{color:#cfcfcf;font-size:10px;text-decoration:none}
</style>
</head>
<body>

<header>
  <div class="photo hero" role="img" aria-label="City street with a glass office tower beside historic stone buildings"></div>
  <div class="abs hero-shade"></div>
  <nav class="abs topnav">
    <a href="#home">Home</a><a href="#about">About us</a><a href="#practice">Practice areas</a><a href="#news">News</a><a href="#malta">About Malta</a><a href="#contact">Contact</a>
  </nav>
  <div class="abs brand">
    <div class="brand-name">Ferris &amp; Delmar</div>
    <div class="brand-sub">Advocates</div>
  </div>
  <p class="abs hero-text">Trusted advocates in Malta, offering clear counsel and firm representation in every matter we take on for our clients.</p>
  <div class="abs btn-ghost">Contact us</div>
  <svg class="abs chevron" width="24" height="14" viewBox="0 0 24 14"><path d="M3 3l9 8 9-8" fill="none" stroke="#fff" stroke-width="2.5"/></svg>
</header>

<section id="about">
  <h2 class="abs section-title" style="top:736px">About us</h2>
  <div class="abs title-rule" style="top:778px"></div>
  <p class="abs intro">We are a Maltese law practice built on integrity, discretion and results, guiding private and corporate clients through every stage of their legal matters.</p>

  <div class="photo" style="left:0;top:907px;width:463px;height:333px;background:linear-gradient(135deg,#d9dde2,#7d8894 55%,#4a5360)" role="img" aria-label="Colleagues meeting around a boardroom table"></div>
  <div class="abs feature-panel" style="left:463px;top:907px;width:737px;height:333px"></div>
  <div class="abs" style="left:558px;top:950px">
    <div class="feature-num">01</div>
    <div class="feature-head" style="margin-top:30px">Our firm</div>
    <p class="feature-text" style="margin-top:18px">Founded in Valletta, our team brings decades of courtroom and advisory experience to each case, large or small.</p>
    <div class="btn-small" style="margin-top:14px">Read more</div>
  </div>

  <div class="abs" style="left:235px;top:1352px">
    <div class="feature-num">02</div>
    <div class="feature-head" style="margin-top:30px">Our values</div>
    <p class="feature-text" style="margin-top:18px">We believe in honest advice, careful preparation and steady communication, so clients always know where they stand.</p>
    <div class="btn-small" style="margin-top:14px">Read more</div>
  </div>
  <div class="photo" style="left:728px;top:1320px;width:472px;height:334px;background:linear-gradient(135deg,#e3e7ee,#3a4d6e 55%,#1d2a44)" role="img" aria-label="Two professionals in suits signing documents"></div>

  <div class="photo" style="left:0;top:1743px;width:463px;height:333px;background:linear-gradient(180deg,#dfe5ec 0%,#b9c2cb 35%,#8a8f94 70%,#5c6770)" role="img" aria-label="Panorama of an old European city with a church spire"></div>
  <div class="abs feature-panel" style="left:463px;top:1743px;width:737px;height:333px"></div>
  <div class="abs" style="left:558px;top:1786px">
    <div class="feature-num">03</div>
    <div class="feature-head" style="margin-top:30px">Offices</div>
    <p class="feature-text" style="margin-top:18px">Our offices sit in the heart of Malta, close to the law courts and within easy reach for clients.</p>
    <div class="btn-small" style="margin-top:14px">Read more</div>
  </div>
</section>

<section id="practice">
  <h2 class="abs section-title" style="top:2158px">Practice areas</h2>
  <div class="abs title-rule" style="top:2200px"></div>

  <div class="abs practice" style="left:190px;top:2266px">
    <div class="practice-icon"><svg width="24" height="24" viewBox="0 0 24 24" fill="none" stroke="#777" stroke-width="1.6"><circle cx="7" cy="15" r="5"/><circle cx="17" cy="15" r="5"/><path d="M10 11l4-6"/></svg></div>
    <div class="practice-name">Criminal</div>
    <p class="practice-text">Defence and advice at every stage of proceedings.</p>
  </div>
  <div class="abs practice" style="left:385px;top:2266px">
    <div class="practice-icon"><svg width="24" height="24" viewBox="0 0 24 24" fill="#777"><circle cx="12" cy="8" r="4"/><path d="M4 21c0-5 4-8 8-8s8 3 8 8z"/></svg></div>
    <div class="practice-name" style="font-size:12px;letter-spacing:1.5px">Sovereign Patron Pathway</div>
    <p class="practice-text">Guidance through residence and investment programmes.</p>
  </div>
  <div class="abs practice" style="left:580px;top:2266px">
    <div class="practice-icon"><svg width="24" height="24" viewBox="0 0 24 24" fill="#777"><path d="M12 3l9 8h-3v9h-4v-6h-4v6H6v-9H3z"/></svg></div>
    <div class="practice-name">Residence</div>
    <p class="practice-text">Citizenship and residence applications handled with care.</p>
  </div>
  <div class="abs practice" style="left:775px;top:2266px">
    <div class="practice-icon"><svg width="26" height="24" viewBox="0 0 26 24" fill="none" stroke="#777" stroke-width="1.6"><path d="M13 3v18M7 21h12M4 7h18M4 7l-3 7h6zM22 7l-3 7h6z"/></svg></div>
    <div class="practice-name">Arbitration</div>
    <p class="practice-text">Arbitration and alternative dispute resolution services.</p>
  </div>

  <div class="abs practice" style="left:190px;top:2476px">
    <div class="practice-icon"><svg width="22" height="24" viewBox="0 0 22 24" fill="#777"><rect x="3" y="2" width="16" height="20"/><path d="M6 7h10M6 11h10M6 15h7" stroke="#f3f3f3" stroke-width="1.5"/></svg></div>
    <div class="practice-name">Criminal defence</div>
    <p class="practice-text">Robust representation before the Maltese courts.</p>
  </div>
  <div class="abs practice" style="left:385px;top:2476px">
    <div class="practice-icon"><svg width="24" height="24" viewBox="0 0 24 24" fill="#777"><path d="M3 9h5l9-5v16l-9-5H3z"/><rect x="6" y="15" width="3" height="6"/></svg></div>
    <div class="practice-name">Media law</div>
    <p class="practice-text">Defamation, publishing and broadcasting law advice.</p>
  </div>
  <div class="abs practice" style="left:580px;top:2476px">
    <div class="practice-icon"><svg width="24" height="24" viewBox="0 0 24 24" fill="#777"><rect x="4" y="5" width="10" height="16"/><rect x="14" y="10" width="6" height="11"/></svg></div>
    <div class="practice-name">Commercial</div>
    <p class="practice-text">Company formation, contracts and corporate matters.</p>
  </div>
  <div class="abs practice" style="left:775px;top:2476px">
    <div class="practice-icon"><svg width="24" height="24" viewBox="0 0 24 24" fill="#777"><rect x="9" y="2" width="9" height="6" transform="rotate(45 13.5 5)"/><path d="M11 10L3 18l2 2 8-8z"/><rect x="13" y="19" width="9" height="3"/></svg></div>
    <div class="practice-name">Civil litigation</div>
    <p class="practice-text">Claims and disputes argued with precision.</p>
  </div>
</section>

<section id="testimonials">
  <div class="photo band" style="top:2749px;height:237px;background:linear-gradient(90deg,#2a2a2a,#3d3d3d 50%,#1f1f1f)" role="img" aria-label="Dark street scene with city traffic"></div>
  <h3 class="abs band-title" style="top:2800px">What others say</h3>
  <p class="abs band-text" style="top:2848px">“Professional, responsive and thorough from start to finish. They explained every step and delivered an outcome beyond our expectations.”</p>
  <p class="abs band-author" style="top:2920px">Martin G.</p>
  <span class="abs arrow" style="left:330px;top:2853px">‹</span>
  <span class="abs arrow" style="left:863px;top:2853px">›</span>
</section>

<section id="news">
  <h2 class="abs section-title" style="top:3093px">Latest news</h2>
  <div class="abs title-rule" style="top:3135px"></div>
  <div class="photo" style="left:0;top:3212px;width:478px;height:323px;background:linear-gradient(135deg,#e9ecef,#9aa3ab 55%,#4f5a63)" role="img" aria-label="Laptop and paperwork on a desk during a meeting"></div>
  <div class="abs" style="left:558px;top:3206px">
    <h3 class="news-title">Lorem Ipsum</h3>
    <p class="news-text" style="margin-top:18px">Our team secured a favourable ruling in a complex commercial dispute heard this month before the Court of Appeal.</p>
    <div class="btn-small" style="margin-top:14px">Read more</div>
  </div>
  <div class="abs" style="left:558px;top:3394px">
    <h3 class="news-title">Nunc a Mauris</h3>
    <p class="news-text" style="margin-top:18px">An update on recent changes to Maltese residence rules and what they mean for applicants and their families.</p>
    <div class="btn-small" style="margin-top:14px">Read more</div>
  </div>
</section>

<section id="malta">
  <div class="photo band" style="top:3656px;height:170px;background:linear-gradient(180deg,#20252b,#3c3b37 60%,#2a2724)" role="img" aria-label="Maltese harbour town at dusk"></div>
  <h3 class="abs band-title" style="top:3690px">About Malta</h3>
  <p class="abs band-text" style="top:3726px;font-style:normal">A small island nation at the centre of the Mediterranean, Malta offers a stable legal system rooted in civil and common law traditions, English as an official language and a welcoming business climate.</p>
</section>

<section id="contact">
  <h2 class="abs section-title" style="top:3997px">Contact</h2>
  <div class="abs title-rule" style="top:4039px"></div>
  <form>
    <label class="abs field-label" style="left:318px;top:4117px">Name</label>
    <div class="abs field" style="left:318px;top:4136px;width:106px;height:22px"></div>
    <label class="abs field-label" style="left:456px;top:4117px">E-mail</label>
    <div class="abs field" style="left:456px;top:4136px;width:106px;height:22px"></div>
    <label class="abs field-label" style="left:318px;top:4194px">Message</label>
    <div class="abs field" style="left:318px;top:4213px;width:244px;height:76px"></div>
    <span class="abs field-label" style="left:534px;top:4306px">Send</span>
  </form>
  <div class="abs contact-side" style="left:610px;top:4114px;width:240px">
    <p>Reach out to us and we will reply within one working day.</p>
    <p style="margin-top:24px">Valletta, Malta</p>
    <p style="margin-top:18px">E-mail: hello@ferrisdelmar.example</p>
    <p style="margin-top:14px"><span class="social-dot"></span><span class="social-dot"></span></p>
  </div>
</section>

<footer>
  <div class="abs site-footer"></div>
  <div class="abs footer-brand">Ferris &amp; Delmar</div>
  <nav class="abs footer-nav">
    <a href="#home">Home</a><a href="#about">About Us</a><a href="#practice">Practice Areas</a><a href="#news">News</a><a href="#malta">About Malta</a><a href="#contact">Contact</a>
  </nav>
</footer>

</body>
</html>
```